We need a business card design, letterhead design and envelope design for our corporate image

We are looking for a corporate business card design, letterhead and envelope design to match the business card design. Logo is done.

```html
<!DOCTYPE html>
<html lang="en">
<head>
<meta charset="utf-8">
<title>Norvane – Business Card</title>
<link rel="stylesheet" href="https://fonts.googleapis.com/css2?family=Source+Sans+3:wght@400;600;700&display=swap">
<style>
  :root {
    --page: #ececea;
    --charcoal: #2a2a2a;
    --paper: #f7f7f7;
    --accent: #f2c800;
    --ink-grey: #5c5c5c;
    --title-grey: #8c8c8c;
    --font: "Source Sans 3", sans-serif;
  }
  * { margin: 0; padding: 0; box-sizing: border-box; }
  html, body { width: 1200px; height: 1200px; overflow: hidden; }
  body { background: var(--page); font-family: var(--font); position: relative; }

  .card {
    position: absolute;
    left: 284px;
    width: 632px;
    height: 360px;
    border-radius: 18px;
    overflow: hidden;
  }
  .card--front { top: 180px; background: var(--paper); }
  .card--back { top: 640px; background: var(--charcoal); display: flex; align-items: center; justify-content: center; }

  .header-band {
    position: absolute; left: 0; top: 0; width: 100%; height: 115px;
    background: var(--charcoal);
  }

  .brand { display: flex; align-items: center; gap: 12px; }
  .brand__square { width: 26px; height: 26px; background: var(--accent); }
  .brand__name { color: var(--accent); font-weight: 600; font-size: 38px; letter-spacing: 0.5px; line-height: 1; }
  .header-band .brand { position: absolute; left: 50px; top: 38px; }

  .brand--large .brand__square { width: 46px; height: 46px; }
  .brand--large .brand__name { font-size: 68px; }
  .brand--large { gap: 20px; }

  .identity { position: absolute; right: 51px; top: 36px; text-align: right; }
  .identity__name { color: var(--accent); font-weight: 700; font-size: 30px; line-height: 1; }
  .identity__title { color: var(--title-grey); font-size: 18px; margin-top: 3px; line-height: 1; }

  .contacts { position: absolute; left: 50px; top: 172px; list-style: none; }
  .contact { display: flex; align-items: center; gap: 16px; height: 34px; margin-bottom: 18px; }
  .contact__icon { width: 34px; height: 34px; border-radius: 50%; background: var(--charcoal); flex: none; display: flex; align-items: center; justify-content: center; }
  .contact__text { color: var(--ink-grey); font-size: 17.5px; line-height: 20px; }

  .corner-mark { position: absolute; left: 487px; top: 215px; width: 145px; height: 145px; }
  .corner-mark__v { position: absolute; left: 0; top: 0; width: 27px; height: 100%; background: var(--accent); }
  .corner-mark__h { position: absolute; left: 0; top: 0; width: 100%; height: 27px; background: var(--accent); }
</style>
</head>
<body>

<section class="card card--front" aria-label="Business card front">
  <header class="header-band">
    <div class="brand">
      <span class="brand__square"></span>
      <span class="brand__name">Norvane</span>
    </div>
    <div class="identity">
      <p class="identity__name">Daniel Hartley</p>
      <p class="identity__title">Managing Director</p>
    </div>
  </header>

  <ul class="contacts">
    <li class="contact">
      <span class="contact__icon">
        <svg width="16" height="16" viewBox="0 0 24 24"><path fill="#f2c800" d="M6.6 10.8a15.1 15.1 0 0 0 6.6 6.6l2.2-2.2c.3-.3.7-.4 1-.2 1.1.4 2.3.6 3.6.6.6 0 1 .4 1 1V20c0 .6-.4 1-1 1A17 17 0 0 1 3 4c0-.6.4-1 1-1h3.5c.6 0 1 .4 1 1 0 1.3.2 2.5.6 3.6.1.3 0 .7-.2 1z"/></svg>
      </span>
      <span class="contact__text">555.014.2087 (Cell)<br>555.014.2090 (Office)</span>
    </li>
    <li class="contact">
      <span class="contact__icon">
        <svg width="18" height="16" viewBox="0 0 24 20"><rect x="2" y="2" width="20" height="15" rx="1.5" fill="none" stroke="#f2c800" stroke-width="2"/><line x1="2" y1="6" x2="22" y2="6" stroke="#f2c800" stroke-width="2"/><path d="M9 12l2 2 4-4" fill="none" stroke="#f2c800" stroke-width="2"/></svg>
      </span>
      <span class="contact__text">hello@norvane.com<br>www.norvane.com</span>
    </li>
    <li class="contact">
      <span class="contact__icon">
        <svg width="16" height="16" viewBox="0 0 24 24"><path fill="#f2c800" d="M12 2a6 6 0 0 0-6 6c0 4.5 6 11 6 11s6-6.5 6-11a6 6 0 0 0-6-6zm0 8.2A2.2 2.2 0 1 1 12 5.8a2.2 2.2 0 0 1 0 4.4z"/><rect x="4" y="20" width="16" height="2" fill="#f2c800"/></svg>
      </span>
      <span class="contact__text">Millbrook, CT USA</span>
    </li>
  </ul>

  <div class="corner-mark" aria-hidden="true">
    <span class="corner-mark__v"></span>
    <span class="corner-mark__h"></span>
  </div>
</section>

<section class="card card--back" aria-label="Business card back">
  <div class="brand brand--large">
    <span class="brand__square"></span>
    <span class="brand__name">Norvane</span>
  </div>
</section>

</body>
</html>
```